Membership Drive "CHRISTMAS SPECIAL"

Looking to run a "Christmas Special" on 6 month Memberships for December 2019 to boost membership number up. This is a great time to get people exercising and everyone loves a Christmas Sale. Special is designed to attract more people to join and enjoy the savings.
Artwork will be display via social media (FP and Pictora) as well as in store. Artwork must be eye catching and direct to the customer. Customer should feel a sense of relief with being able to exercise at a lower cost .

Heading: "Christmas Sale"
6 Months
$199.00 Save over 30%
Terms and conditions apply"
*Offer End 31st December

below are other promos we had designed on Sketch Harbor along with potential photos to be included into this promo

Target Market(s)

Males and Females aged between 16 - 45

Industry/Entity Type

Fitness

Colors

Designer to choose colors to be used in the design.

Requirements
Must have
• Must emphasize "Christmas Special" $199.00 Save over 30%
• Terms and conditions apply
• Offer Ends 31st of December
• "All of our contact details"
• Address: 14 Marlow Rd Fernhill 3187
• Ph: 9428 7160
• www.stridelane.com.au
• Design format must come in PDF for a AO poster and an Pictora format please
Nice to have
• Some Christmas feels to the artwork

```html
<!DOCTYPE html>
<html lang="en">
<head>
<meta charset="utf-8">
<title>Super Christmas Special – Stridelane Gymnasium</title>
<link rel="stylesheet" href="https://fonts.googleapis.com/css2?family=Great+Vibes&family=Josefin+Sans:wght@200;300;600;700&family=Montserrat:wght@700;800&display=swap">
<style>
  :root {
    --festive-red: #e3344a;
    --pine-dark: #1f7a4f;
    --pine-mid: #2f9a63;
    --pine-light: #7ccf5a;
    --photo-deep: #7e2f3b;
    --photo-mid: #a8505c;
    --photo-soft: #c97c84;
    --white: #ffffff;
    --ink: #111111;
    --intro-ink: #2a1a1d;
  }
  * { margin: 0; padding: 0; box-sizing: border-box; }
  html, body {
    width: 849px; height: 1200px; overflow: hidden;
    background: var(--festive-red);
  }
  .poster {
    position: relative; width: 849px; height: 1200px;
    background: var(--festive-red); overflow: hidden;
  }
  .poster-art { position: absolute; inset: 0; display: block; }
  .intro { font-family: "Josefin Sans", sans-serif; font-weight: 300; fill: var(--intro-ink); }
  .headline-script { font-family: "Great Vibes", cursive; fill: var(--white); }
  .headline-bold { font-family: "Montserrat", sans-serif; font-weight: 800; fill: var(--ink); }
  .headline-thin { font-family: "Josefin Sans", sans-serif; font-weight: 200; fill: var(--white); }
  .discount { font-family: "Montserrat", sans-serif; font-weight: 800; fill: var(--ink); }
  .offer-end { font-family: "Josefin Sans", sans-serif; font-weight: 600; fill: var(--ink); }
  .price { font-family: "Montserrat", sans-serif; font-weight: 700; fill: var(--white); }
  .saving { font-family: "Josefin Sans", sans-serif; font-weight: 600; fill: var(--white); }
  .brand-name { font-family: "Montserrat", sans-serif; font-weight: 800; fill: var(--ink); }
  .contact { font-family: "Josefin Sans", sans-serif; font-weight: 600; fill: var(--white); font-variant: small-caps; }
  .terms { font-family: "Josefin Sans", sans-serif; font-weight: 600; fill: var(--white); font-variant: small-caps; }
</style>
</head>
<body>
<main class="poster">
  <svg class="poster-art" width="849" height="1200" viewBox="0 0 849 1200" xmlns="http://www.w3.org/2000/svg">
    <defs>
      <linearGradient id="garlandTop" x1="0" y1="0" x2="0" y2="1">
        <stop offset="0" stop-color="var(--pine-dark)"/>
        <stop offset="0.7" stop-color="var(--pine-mid)"/>
        <stop offset="1" stop-color="var(--pine-light)"/>
      </linearGradient>
      <linearGradient id="garlandBottom" x1="0" y1="0" x2="0" y2="1">
        <stop offset="0" stop-color="var(--pine-light)"/>
        <stop offset="0.35" stop-color="var(--pine-mid)"/>
        <stop offset="1" stop-color="var(--pine-dark)"/>
      </linearGradient>
      <linearGradient id="photoTone" x1="0" y1="0" x2="1" y2="1">
        <stop offset="0" stop-color="var(--photo-soft)"/>
        <stop offset="0.5" stop-color="var(--photo-mid)"/>
        <stop offset="1" stop-color="var(--photo-deep)"/>
      </linearGradient>
    </defs>

    <!-- pine garlands -->
    <rect class="garland garland-top" x="0" y="0" width="849" height="250" fill="url(#garlandTop)"
          role="img" aria-label="Pine branch garland along the top edge"/>
    <rect class="garland garland-bottom" x="0" y="965" width="849" height="235" fill="url(#garlandBottom)"
          role="img" aria-label="Pine branch garland along the bottom edge"/>

    <!-- white frame -->
    <rect class="frame" x="145.5" y="254.5" width="558" height="728" fill="none" stroke="var(--white)" stroke-width="9"/>

    <!-- photo panel -->
    <rect class="photo-panel" x="178" y="286" width="500" height="666" fill="url(#photoTone)"
          role="img" aria-label="Photo of a muscular athlete lifting dumbbells in a smoky gym, tinted red"/>

    <!-- intro line -->
    <text class="intro" x="425" y="323" text-anchor="middle" font-size="28">Start your new year resolution with</text>
    <text class="intro" x="425" y="359" text-anchor="middle" font-size="28">our Christmas off</text>

    <!-- headline -->
    <text class="headline-script" x="428" y="468" text-anchor="middle" font-size="165">Super</text>
    <text class="headline-bold" x="424" y="559" text-anchor="middle" font-size="104" textLength="609" lengthAdjust="spacingAndGlyphs">CHRISTMAS</text>
    <text class="headline-thin" x="414" y="638" text-anchor="middle" font-size="88" textLength="316" lengthAdjust="spacingAndGlyphs">SPECIAL</text>

    <!-- discount banner -->
    <polygon class="discount-banner" points="199,675 649,675 625,761 175,761" fill="var(--white)"/>
    <text class="discount" x="428" y="745" text-anchor="middle" font-size="76" textLength="361" lengthAdjust="spacingAndGlyphs">30%OFF*</text>
    <text class="offer-end" x="533" y="782" text-anchor="middle" font-size="12.5">Offer Ends 31st of December</text>

    <!-- price block -->
    <text class="price" x="425" y="878" text-anchor="middle" font-size="64" textLength="280" lengthAdjust="spacingAndGlyphs">$199.00</text>
    <text class="saving" x="425" y="922" text-anchor="middle" font-size="34" textLength="271" lengthAdjust="spacingAndGlyphs">SAVE OVER 30%</text>
    <text class="saving" x="425" y="945" text-anchor="middle" font-size="19" textLength="280" lengthAdjust="spacingAndGlyphs">WITH 6 MONTHS SUBSCRIPTION</text>

    <!-- brand and contact -->
    <text class="brand-name" x="15" y="1118" font-size="27" textLength="140" lengthAdjust="spacingAndGlyphs">STRIDELANE</text>
    <text class="contact" x="18" y="1152" font-size="12">Address: 14 Marlow Rd Fernhill 3187</text>
    <text class="contact" x="19" y="1170" font-size="12">Ph: 9428 7160</text>
    <text class="contact" x="18" y="1188" font-size="11">www.stridelane.com.au</text>
    <text class="terms" x="832" y="1188" text-anchor="end" font-size="11.5">*Terms and conditions apply</text>
  </svg>
</main>
</body>
</html>
```